Accountability Project Graphics

I want to create 10 social media graphics (new Instagram size 4:5 (1080 x 1350 pixels) focusing on our Quilvo Accountability App, using any of the 3 pictures attached. Use the attached pics only, NO RANDOM STOCK PHOTOGRAPHY. For the color scheme, use the landing page colors/fonts (attached).
You can add any of the 3 photos attached but I mainly need BOLD text that includes these headlines and sub-headlines on them.
Please NOTE for all the headlines below, also add this sub-headline on each graphic:
Stay Consistent with RT in Your Pocket!
Here are the headlines:
• Stop Starting Over Every Monday
• You don't need more willpower. You need more support
• Built for women who are tired of doing this alone
• When Motivation Fades, RT Checks In
• The Support System You've Been Missing
• Support When Motivation Disappears
• What if RT Checked in Every Day?
• The Missing Piece Isn't Another Diet
• Eat the food you love. Stay accountable every day.
• One Bad Meal Doesn't Mean You Failed
women over 40 trying to lose weight

```html
<!DOCTYPE html>
<html lang="en">
<head>
<meta charset="utf-8">
<title>Stop Starting Over Every Monday</title>
<link rel="stylesheet" href="https://fonts.googleapis.com/css2?family=Bebas+Neue&family=Montserrat:wght@600&display=swap">
<style>
  :root {
    --plum-deep: #351640;
    --plum: #5e2550;
    --rose: #c24a78;
    --rose-light: #e07aa0;
    --accent: #d84f7d;
    --white: #ffffff;
  }
  html, body {
    margin: 0;
    padding: 0;
    width: 960px;
    height: 1200px;
    overflow: hidden;
  }
  .poster {
    position: relative;
    width: 960px;
    height: 1200px;
    overflow: hidden;
    background: linear-gradient(100deg, var(--plum-deep) 0%, var(--plum) 38%, var(--rose) 78%, #cf5a86 100%);
  }
  .decor {
    position: absolute;
    inset: 0;
    width: 960px;
    height: 1200px;
  }
  .portrait {
    position: absolute;
    left: 418px;
    top: 133px;
    width: 520px;
    height: 978px;
    border-radius: 240px 240px 0 0;
    background: linear-gradient(180deg, #2a1a22 0%, #5a3a3a 22%, #1c1418 45%, #141014 100%);
    opacity: 0.92;
  }
  .headline {
    position: absolute;
    left: 71px;
    top: 158px;
    margin: 0;
    font-family: "Bebas Neue", "Oswald", sans-serif;
    font-weight: 400;
    font-size: 166px;
    line-height: 162px;
    letter-spacing: 1px;
    color: var(--white);
  }
  .headline span { display: block; }
  .headline .accent { color: var(--accent); }
  .footer-band {
    position: absolute;
    left: 0;
    bottom: 0;
    width: 960px;
    height: 89px;
    background: var(--accent);
  }
  .tagline {
    position: absolute;
    left: 0;
    width: 960px;
    top: 1137px;
    margin: 0;
    text-align: center;
    font-family: "Montserrat", sans-serif;
    font-weight: 600;
    font-size: 28px;
    line-height: 34px;
    color: var(--white);
  }
  .code {
    position: absolute;
    left: 898px;
    top: 1158px;
    font-family: "Montserrat", sans-serif;
    font-weight: 600;
    font-size: 12px;
    color: var(--white);
  }
  .app-badge {
    position: absolute;
    left: 56px;
    top: 1065px;
    width: 88px;
    height: 88px;
  }
</style>
</head>
<body>
  <main class="poster">
    <svg class="decor" viewBox="0 0 960 1200" aria-hidden="true">
      <circle cx="150" cy="560" r="380" fill="none" stroke="#ffffff" stroke-opacity="0.06" stroke-width="60"/>
      <circle cx="150" cy="560" r="470" fill="none" stroke="#ffffff" stroke-opacity="0.04" stroke-width="30"/>
      <circle cx="900" cy="820" r="210" fill="#e07aa0" fill-opacity="0.35"/>
      <circle cx="880" cy="420" r="320" fill="none" stroke="#ffffff" stroke-opacity="0.08" stroke-width="40"/>
    </svg>

    <div class="portrait" role="img" aria-label="Smiling coach with long dark hair in a black mesh and lace top, hand on hip"></div>

    <h1 class="headline">
      <span>Stop</span>
      <span class="accent">Starting</span>
      <span class="accent">Over</span>
      <span>Every</span>
      <span>Monday</span>
    </h1>

    <div class="footer-band"></div>
    <p class="tagline">STAY CONSISTENT WITH RT IN YOUR POCKET!</p>
    <span class="code">C58</span>

    <svg class="app-badge" viewBox="0 0 88 88" aria-hidden="true">
      <circle cx="44" cy="44" r="44" fill="#d84f7d"/>
      <g fill="none" stroke="#ffffff" stroke-width="2" stroke-linecap="round" stroke-linejoin="round">
        <rect x="22" y="24" width="34" height="26" rx="2"/>
        <line x1="28" y1="58" x2="44" y2="58"/>
        <line x1="36" y1="50" x2="36" y2="58"/>
        <rect x="46" y="34" width="20" height="32" rx="3" fill="#d84f7d"/>
        <circle cx="56" cy="50" r="6"/>
        <polyline points="53,50 55.5,52.5 59,48"/>
        <circle cx="30" cy="32" r="4"/>
      </g>
    </svg>
  </main>
</body>
</html>
```